Vantiqo custom business card design

Need a authentic, innovative business card design for a new mobile app business. I am uploading a few screen images from our app for you to view. I would like app design theme to match business card design. I can also send logo images.

```html
<!DOCTYPE html>
<html lang="en">
<head>
<meta charset="utf-8">
<title>Vantiqo Business Card</title>
<link href="https://fonts.googleapis.com/css2?family=Roboto:wght@400;500;700;900&display=swap" rel="stylesheet">
<style>
  :root {
    --stage: #2a2a2c;
    --ink-black: #050505;
    --brand-purple: #63068f;
    --paper-white: #ffffff;
    --logo-dark: #222222;
  }
  * { margin: 0; padding: 0; box-sizing: border-box; }
  html, body {
    width: 1200px;
    height: 874px;
    overflow: hidden;
    background: var(--stage);
    font-family: "Roboto", Arial, sans-serif;
  }
  .canvas {
    position: relative;
    width: 1200px;
    height: 874px;
  }
  .card {
    position: absolute;
    left: 320px;
    width: 560px;
    height: 320px;
    overflow: hidden;
    box-shadow: 0 10px 30px rgba(0,0,0,0.45);
  }
  /* Back side */
  .card-back {
    top: 97px;
    background: var(--ink-black);
    color: var(--paper-white);
  }
  .back-brand {
    position: absolute;
    left: 0; right: 0;
    top: 112px;
    display: flex;
    align-items: center;
    justify-content: center;
    gap: 14px;
  }
  .brand-dot {
    width: 30px; height: 30px;
    border-radius: 50%;
    background: var(--paper-white);
  }
  .back-brand .brand-name {
    font-size: 48px;
    font-weight: 700;
    letter-spacing: 0.5px;
  }
  .back-web {
    position: absolute;
    left: 0; right: 0;
    bottom: 44px;
    text-align: center;
    font-size: 15px;
    letter-spacing: 9px;
  }
  /* Front side */
  .card-front {
    top: 457px;
    background: var(--brand-purple);
    color: var(--paper-white);
  }
  .front-shape {
    position: absolute;
    inset: 0;
  }
  .contact-block {
    position: absolute;
    left: 38px;
    top: 34px;
  }
  .person-name {
    font-size: 24px;
    font-weight: 700;
    letter-spacing: 0.3px;
    line-height: 1;
  }
  .person-role {
    font-size: 15px;
    font-weight: 500;
    margin-top: 4px;
  }
  .address {
    font-size: 14px;
    line-height: 1.3;
    margin-top: 18px;
  }
  .contact-list {
    list-style: none;
    margin-top: 18px;
    font-size: 14px;
  }
  .contact-list li {
    display: flex;
    align-items: center;
    gap: 10px;
    height: 21px;
  }
  .contact-list svg {
    width: 13px; height: 13px;
    fill: var(--paper-white);
    flex: none;
  }
  .front-brand {
    position: absolute;
    left: 345px;
    top: 136px;
    display: flex;
    align-items: center;
    gap: 12px;
    color: var(--logo-dark);
  }
  .front-brand .brand-dot {
    width: 26px; height: 26px;
    background: var(--brand-purple);
  }
  .front-brand .brand-name {
    font-size: 42px;
    font-weight: 700;
  }
</style>
</head>
<body>
<main class="canvas">

  <section class="card card-back" aria-label="Card back">
    <div class="back-brand">
      <span class="brand-dot"></span>
      <span class="brand-name">Vantiqo</span>
    </div>
    <p class="back-web">www.vantiqo.com</p>
  </section>

  <section class="card card-front" aria-label="Card front">
    <svg class="front-shape" viewBox="0 0 560 320" preserveAspectRatio="none" aria-hidden="true">
      <path d="M340,0 C275,40 255,120 300,172 C235,220 228,282 272,320 L560,320 L560,0 Z" fill="var(--paper-white)"/>
    </svg>

    <div class="contact-block">
      <h1 class="person-name">MARCUS HALE</h1>
      <p class="person-role">CEO/FOUNDER</p>
      <p class="address">2140 Alder Court<br>Juneau, Alaska 34190</p>
      <ul class="contact-list">
        <li>
          <svg viewBox="0 0 24 24"><path d="M6.6 10.8a15 15 0 0 0 6.6 6.6l2.2-2.2c.3-.3.7-.4 1-.2 1.1.4 2.3.6 3.6.6.6 0 1 .4 1 1V20c0 .6-.4 1-1 1A17 17 0 0 1 3 4c0-.6.4-1 1-1h3.5c.6 0 1 .4 1 1 0 1.3.2 2.5.6 3.6.1.3 0 .7-.2 1z"/></svg>
          512 904 3318
        </li>
        <li>
          <svg viewBox="0 0 24 24"><path d="M7 1h10a2 2 0 0 1 2 2v18a2 2 0 0 1-2 2H7a2 2 0 0 1-2-2V3a2 2 0 0 1 2-2zm0 3v14h10V4zm5 15.5a1 1 0 1 0 0 2 1 1 0 0 0 0-2z"/></svg>
          741 226 8053
        </li>
        <li>
          <svg viewBox="0 0 24 24"><path d="M7 2h10v5H7zM4 8h16a2 2 0 0 1 2 2v7h-4v5H6v-5H2v-7a2 2 0 0 1 2-2zm4 8v4h8v-4z"/></svg>
          390 571 2864
        </li>
        <li>
          <svg viewBox="0 0 24 24"><path d="M2 5h20v14H2zm2 2v.5l8 5 8-5V7zm0 3v7h16v-7l-8 5z"/></svg>
          marcus@vantiqo.com
        </li>
        <li>
          <svg viewBox="0 0 24 24"><path d="M12 2a10 10 0 1 0 0 20 10 10 0 0 0 0-20zm-1 17.9A8 8 0 0 1 4.1 10L9 15v1a2 2 0 0 0 2 2zm6.9-2.5A2 2 0 0 0 16 16h-1v-3a1 1 0 0 0-1-1H8v-2h2a1 1 0 0 0 1-1V7h2a2 2 0 0 0 2-2v-.4a8 8 0 0 1 2.9 12.8z"/></svg>
          www.vantiqo.com
        </li>
      </ul>
    </div>

    <div class="front-brand">
      <span class="brand-dot"></span>
      <span class="brand-name">Vantiqo</span>
    </div>
  </section>

</main>
</body>
</html>
```